BRIGHT CORAL INC , CELL PHONE STORE

We need website design . we already have one but not happy with it www.brightcoralinc.example
we cell phones provide service ,phone repair ,
phone accessories.
online sale payment via PayVerra
shipping by QDMX

Industry/Entity Type

Cell Phone

Number of Pages Required

5+ page

Font styles to use
Serif
Sans Serif

Colors
3176b5

Requirements
Must have
• online sale via PayVerra
Nice to have
• email address

```html
<!DOCTYPE html>
<html lang="en">
<head>
<meta charset="utf-8">
<title>Bright Coral Inc — Cell Phone Store</title>
<link href="https://fonts.googleapis.com/css2?family=Open+Sans:wght@400;600;700&display=swap" rel="stylesheet">
<style>
:root{
  --brand-blue:#3a8fd6;
  --brand-deep:#3176b5;
  --coral:#e2463a;
  --ink:#222;
  --muted:#777;
  --line:#e3e3e3;
  --soft:#f5f5f5;
  --star:#f2c21b;
  --white:#fff;
}
*{box-sizing:border-box;margin:0;padding:0}
html,body{width:1200px;height:2736px;overflow:hidden;background:var(--white);font-family:"Open Sans",Arial,sans-serif;color:var(--ink)}
.page{position:relative;width:1200px;height:2736px;border-top:5px solid var(--coral);overflow:hidden}
.wrap{width:1022px;margin:0 auto;position:relative}
/* header */
.topbar{height:100px;display:flex;align-items:center;justify-content:space-between}
.phone{display:flex;align-items:center;gap:12px;font-size:19px;color:#333}
.logo{position:absolute;left:50%;transform:translateX(-50%);font-size:27px;font-weight:700;color:var(--coral);letter-spacing:1px;display:flex;align-items:center;gap:8px;white-space:nowrap}
.logo .dot{width:10px;height:10px;border-radius:50%;background:var(--coral)}
.util{font-size:13px;color:#666;letter-spacing:.5px}
.util b{color:var(--brand-blue);font-weight:400}
.nav{height:72px;display:flex;align-items:center;justify-content:space-between;border-bottom:1px solid var(--line)}
.nav a{font-size:16px;color:#333;text-decoration:none;letter-spacing:.5px;padding:4px 18px}
.nav a.active{border:1px solid var(--brand-blue);border-radius:16px;color:var(--brand-blue)}
/* hero */
.hero{height:503px;background:linear-gradient(#f4f4f4,#ececec);border-bottom:1px solid var(--line);position:relative}
.hero-art{position:absolute;left:130px;top:50px;width:360px;height:400px;border-radius:14px;background:radial-gradient(circle at 50% 40%,#4a9bd4 0,#2d3a46 45%,#e9e9e9 70%)}
.hero-copy{position:absolute;left:676px;top:170px;width:470px}
.hero-copy h1{font-size:44px;font-weight:400;color:var(--brand-blue);letter-spacing:1px;white-space:nowrap;line-height:56px}
.hero-copy p{font-size:20px;color:#444;line-height:29px;margin-top:6px;width:440px}
.btn{display:inline-block;margin-top:22px;background:var(--coral);color:#fff;font-size:16px;padding:8px 24px;border-radius:18px}
.slider-arrows{position:absolute;right:40px;top:400px;display:flex;gap:6px}
.slider-arrows span{width:26px;height:26px;border-radius:50%;background:#777;color:#fff;font-size:16px;display:flex;align-items:center;justify-content:center}
/* services */
.services{height:482px;display:flex;justify-content:space-between;padding:66px 0 0}
.service{width:290px;text-align:center}
.service .thumb{width:176px;height:176px;border-radius:50%;margin:0 auto;border:4px solid #eee}
.service h3{font-size:20px;font-weight:400;margin-top:24px;letter-spacing:.5px}
.service p{font-size:13px;color:var(--muted);line-height:20px;margin-top:14px}
.service a{display:block;font-size:14px;color:var(--brand-blue);margin-top:12px;text-decoration:none}
/* products */
.products{background:var(--soft);height:976px;padding-top:40px}
.products h2{text-align:center;font-size:27px;font-weight:400;letter-spacing:.5px}
.tabs{display:flex;justify-content:center;gap:56px;margin-top:18px;font-size:15px}
.tabs .on{color:var(--brand-blue)}
.grid{display:grid;grid-template-columns:repeat(4,241px);gap:38px 19px;justify-content:space-between;margin-top:66px}
.card{background:#fff;border:1px solid #ddd;height:334px;box-shadow:0 1px 3px rgba(0,0,0,.08)}
.card .img{height:204px;margin:8px 20px 0}
.card .name{background:#f3f3f3;text-align:center;font-size:14px;height:40px;line-height:40px;margin:0 8px}
.card .meta{display:flex;justify-content:space-between;align-items:center;height:42px;padding:0 16px 0 22px}
.price{color:var(--coral);font-size:18px}
.stars{color:var(--star);font-size:18px;letter-spacing:1px}
.stars i{font-style:normal;color:#ccc}
.actions{display:grid;grid-template-columns:repeat(4,1fr);height:40px;border-top:1px solid var(--line)}
.actions span{display:flex;align-items:center;justify-content:center;border-left:1px solid var(--line)}
.actions span:first-child{background:var(--brand-blue);border:0}
/* news */
.news{height:306px;background:linear-gradient(90deg,#3a8dd6,#2f7fcc);color:#fff;padding-top:42px}
.news h2{text-align:center;font-size:27px;font-weight:400}
.news-list{display:flex;justify-content:space-between;margin-top:40px}
.post{display:flex;gap:16px;width:480px}
.post .pic{width:162px;height:142px;flex:none}
.post .body{width:302px}
.post h4{font-size:15px;font-weight:400}
.post time{display:block;font-size:13px;margin-top:6px}
.post p{font-size:11.2px;line-height:21px;margin-top:4px;letter-spacing:-.1px}
.post a{font-size:13px;color:#fff;text-decoration:none}
/* footer */
.footer{padding-top:52px}
.foot-cols{display:flex;height:170px}
.ship-name{width:130px;padding-top:52px;text-align:center;font-size:22px;font-weight:700;color:var(--ink);letter-spacing:1px}
.col h5{font-size:15px;font-weight:400;letter-spacing:.5px;margin-bottom:18px;white-space:nowrap}
.col p{font-size:12px;color:#555;line-height:24px}
.contact{margin-left:68px;width:340px}
.mailing{width:320px}
.subscribe{display:flex;margin-top:12px}
.subscribe span{width:150px;height:30px;border:1px solid #ccc;font-size:12px;color:#888;padding:6px 8px}
.subscribe b{background:var(--coral);color:#fff;font-weight:400;font-size:12px;padding:6px 8px}
.follow{margin-left:auto;text-align:right}
.socials{display:flex;gap:14px;justify-content:flex-end}
.socials span{width:22px;height:22px;border-radius:3px;background:#444}
.bottom{border-top:1px solid var(--line);height:62px;display:flex;justify-content:space-between;align-items:center}
.pay{display:flex;gap:6px}
.pay span{font-size:10px;font-weight:700;color:#244c88;border:1px solid #ccc;padding:4px 5px}
.copy{font-size:12px;color:#333}
</style>
</head>
<body>
<div class="page">
  <header class="wrap">
    <div class="topbar">
      <div class="phone">
        <svg width="16" height="16" viewBox="0 0 16 16"><rect width="16" height="16" rx="3" fill="#3a8fd6"/><path d="M5 4c1 0 2 2 1.5 2.5L6 7c.5 1.2 1.6 2.4 3 3l.6-.6C10 9 12 10 12 11s-1 1.5-2 1.2C7 11.5 4.5 9 3.8 6 3.5 5 4 4 5 4z" fill="#fff"/></svg>
        02 5550 1234
      </div>
      <div class="logo">BRIGHT CORAL INC<span class="dot"></span></div>
      <div class="util">SHIPPING ˅ &nbsp;| &nbsp;SHOPPING CART &nbsp;<b>🛒 : 0</b></div>
    </div>
    <nav class="nav">
      <a class="active">HOME</a><a>ABOUT US</a><a>PRODUCTS</a><a>REPAIR</a><a>SHOP</a><a>AZ</a><a>BILL PAYMENT</a><a>NEWS</a><a>CONTACT US</a>
    </nav>
  </header>

  <section class="hero">
    <div class="hero-art" role="img" aria-label="Smartphone with earphones wrapped around it"></div>
    <div class="hero-copy">
      <h1>BRIGHT CORAL INC</h1>
      <p>Neque porro quisquam est qui dolorem ipsum quia dolor sitdolorem ipsum quia dolor</p>
      <span class="btn">Buy now »</span>
    </div>
    <div class="slider-arrows"><span>‹</span><span>›</span></div>
  </section>

  <section class="wrap services">
    <div class="service">
      <div class="thumb" role="img" aria-label="Hand holding a phone" style="background:radial-gradient(#b9cfe6,#6e92b8)"></div>
      <h3>PHONE SERVICE</h3>
      <p>It has survived not only five centuries, but also the leap into electronic typesetting, remaining essentially unchanged.</p>
      <a>Read More -&gt;</a>
    </div>
    <div class="service">
      <div class="thumb" role="img" aria-label="Phone being repaired with tools" style="background:radial-gradient(#d9dde2,#5b636d)"></div>
      <h3>PHONE REPAIR</h3>
      <p>It has survived not only five centuries, but also the leap into electronic typesetting, remaining essentially unchanged.</p>
      <a>Read More -&gt;</a>
    </div>
    <div class="service">
      <div class="thumb" role="img" aria-label="White earphones" style="background:radial-gradient(#eef3f7,#9fb3c4)"></div>
      <h3>PHONE ACCESSORIES</h3>
      <p>It has survived not only five centuries, but also the leap into electronic typesetting, remaining essentially unchanged.</p>
      <a>Read More -&gt;</a>
    </div>
  </section>

  <section class="products">
    <div class="wrap">
      <h2>OUR PRODUCTS</h2>
      <div class="tabs"><span class="on">Featured</span><span>New Arrivals</span><span>Best Seller</span></div>
      <div class="grid">
        <article class="card"><div class="img" role="img" aria-label="Group of smartphones" style="background:linear-gradient(135deg,#d8d8d8,#333 60%,#e8b44a)"></div><div class="name">Product Name</div><div class="meta"><span class="price">$60.00</span><span class="stars">★★★★<i>☆</i></span></div><div class="actions"><span><svg width="18" height="16"><path d="M1 2h3l2 8h9l2-6H5" stroke="#fff" stroke-width="2" fill="none"/><circle cx="7" cy="14" r="1.5" fill="#fff"/><circle cx="14" cy="14" r="1.5" fill="#fff"/></svg></span><span style="color:#bbb">♥</span><span style="color:#999">⇄</span><span style="color:#999">◎</span></div></article>
        <article class="card"><div class="img" role="img" aria-label="Prepaid SIM cards" style="background:linear-gradient(135deg,#111,#f2d41c 55%,#2a8fd0)"></div><div class="name">Product Name</div><div class="meta"><span class="price">$60.00</span><span class="stars">★★★★<i>☆</i></span></div><div class="actions"><span><svg width="18" height="16"><path d="M1 2h3l2 8h9l2-6H5" stroke="#fff" stroke-width="2" fill="none"/><circle cx="7" cy="14" r="1.5" fill="#fff"/><circle cx="14" cy="14" r="1.5" fill="#fff"/></svg></span><span style="color:#bbb">♥</span><span style="color:#999">⇄</span><span style="color:#999">◎</span></div></article>
        <article class="card"><div class="img" role="img" aria-label="Green SIM card pack" style="background:linear-gradient(#fff,#8cc63f 30%,#8cc63f 80%,#fff)"></div><div class="name">Product Name</div><div class="meta"><span class="price">$60.00</span><span class="stars">★★★★<i>☆</i></span></div><div class="actions"><span><svg width="18" height="16"><path d="M1 2h3l2 8h9l2-6H5" stroke="#fff" stroke-width="2" fill="none"/><circle cx="7" cy="14" r="1.5" fill="#fff"/><circle cx="14" cy="14" r="1.5" fill="#fff"/></svg></span><span style="color:#bbb">♥</span><span style="color:#999">⇄</span><span style="color:#999">◎</span></div></article>
        <article class="card"><div class="img" role="img" aria-label="Black smartphone front view" style="background:linear-gradient(90deg,#fff 25%,#111 25%,#111 75%,#fff 75%)"></div><div class="name">Product Name</div><div class="meta"><span class="price">$60.00</span><span class="stars">★★★★<i>☆</i></span></div><div class="actions"><span><svg width="18" height="16"><path d="M1 2h3l2 8h9l2-6H5" stroke="#fff" stroke-width="2" fill="none"/><circle cx="7" cy="14" r="1.5" fill="#fff"/><circle cx="14" cy="14" r="1.5" fill="#fff"/></svg></span><span style="color:#bbb">♥</span><span style="color:#999">⇄</span><span style="color:#999">◎</span></div></article>
        <article class="card"><div class="img" role="img" aria-label="Purple mobile SIM card" style="background:linear-gradient(#fff 20%,#5b3a9e 20%,#5b3a9e 70%,#fff 70%)"></div><div class="name">Product Name</div><div class="meta"><span class="price">$60.00</span><span class="stars">★★★★<i>☆</i></span></div><div class="actions"><span><svg width="18" height="16"><path d="M1 2h3l2 8h9l2-6H5" stroke="#fff" stroke-width="2" fill="none"/><circle cx="7" cy="14" r="1.5" fill="#fff"/><circle cx="14" cy="14" r="1.5" fill="#fff"/></svg></span><span style="color:#bbb">♥</span><span style="color:#999">⇄</span><span style="color:#999">◎</span></div></article>
        <article class="card"><div class="img" role="img" aria-label="Phone cases and charger" style="background:linear-gradient(135deg,#fff,#1a1a1a 40%,#c9ccd0 70%,#fff)"></div><div class="name">Product Name</div><div class="meta"><span class="price">$60.00</span><span class="stars">★★★★<i>☆</i></span></div><div class="actions"><span><svg width="18" height="16"><path d="M1 2h3l2 8h9l2-6H5" stroke="#fff" stroke-width="2" fill="none"/><circle cx="7" cy="14" r="1.5" fill="#fff"/><circle cx="14" cy="14" r="1.5" fill="#fff"/></svg></span><span style="color:#bbb">♥</span><span style="color:#999">⇄</span><span style="color:#999">◎</span></div></article>
        <article class="card"><div class="img" role="img" aria-label="Black smartphone back view" style="background:linear-gradient(90deg,#fff 32%,#0d0d0d 32%,#2a2a2a 68%,#fff 68%)"></div><div class="name">Product Name</div><div class="meta"><span class="price">$60.00</span><span class="stars">★★★★<i>☆</i></span></div><div class="actions"><span><svg width="18" height="16"><path d="M1 2h3l2 8h9l2-6H5" stroke="#fff" stroke-width="2" fill="none"/><circle cx="7" cy="14" r="1.5" fill="#fff"/><circle cx="14" cy="14" r="1.5" fill="#fff"/></svg></span><span style="color:#bbb">♥</span><span style="color:#999">⇄</span><span style="color:#999">◎</span></div></article>
        <article class="card"><div class="img" role="img" aria-label="Dark SIM card" style="background:linear-gradient(#fff 38%,#111 38%,#1d3b1d 62%,#fff 62%)"></div><div class="name">Product Name</div><div class="meta"><span class="price">$60.00</span><span class="stars">★★★★<i>☆</i></span></div><div class="actions"><span><svg width="18" height="16"><path d="M1 2h3l2 8h9l2-6H5" stroke="#fff" stroke-width="2" fill="none"/><circle cx="7" cy="14" r="1.5" fill="#fff"/><circle cx="14" cy="14" r="1.5" fill="#fff"/></svg></span><span style="color:#bbb">♥</span><span style="color:#999">⇄</span><span style="color:#999">◎</span></div></article>
      </div>
    </div>
  </section>

  <section class="news">
    <div class="wrap">
      <h2>LATEST NEWS</h2>
      <div class="news-list">
        <article class="post">
          <div class="pic" role="img" aria-label="Smartphone with earphones on a table" style="background:linear-gradient(135deg,#ddd,#555)"></div>
          <div class="body"><h4>Nemo Enim Ipsam Volup</h4><time>09-07-2016</time><p>Lorem Ipsum has been the industry's standard dummy text ever since the 1500s, when an unknown printer took a galley of type and scrambled it to make a type specimen</p><a>Read More &gt;&gt;</a></div>
        </article>
        <article class="post">
          <div class="pic" role="img" aria-label="Delivery parcel being handed over" style="background:linear-gradient(135deg,#f3e3b8,#c9a266)"></div>
          <div class="body"><h4>Nemo Enim Ipsam Volup</h4><time>09-07-2016</time><p>Lorem Ipsum has been the industry's standard dummy text ever since the 1500s, when an unknown printer took a galley of type and scrambled it to make a type specimen</p><a>Read More &gt;&gt;</a></div>
        </article>
      </div>
    </div>
  </section>

  <footer class="wrap footer">
    <div class="foot-cols">
      <div class="ship-name">QDMX</div>
      <div class="col contact">
        <h5>CONTACT US</h5>
        <p>Address : 48 Harbor Lane EASTVALE, NY 10000.<br>1 212 555 0148<br>Phone : 02 5550 1234<br>Email : info@brightcoral.example</p>
      </div>
      <div class="col mailing">
        <h5>JOIN OUR MAILING LIST</h5>
        <p style="line-height:18px">Your about us information would fit<br>here nicely.</p>
        <div class="subscribe"><span>Email address</span><b>Submit</b></div>
      </div>
      <div class="col follow">
        <h5>FOLLOW US OUT THERE</h5>
        <div class="socials" role="img" aria-label="Social network links"><span></span><span></span><span></span><span></span></div>
      </div>
    </div>
    <div class="bottom">
      <div class="pay"><span>PayVerra</span><span>Meridex</span><span>Nuvo</span><span>Tallis</span><span>Amplo</span></div>
      <div class="copy">Copyright © 2017. All Rights Reserved</div>
    </div>
  </footer>
</div>
</body>
</html>
```